Specialised investor in e-mobility and energy wants business card design

We need a business card design that fits our existing corporate design. <The look and feel must be 'sharp'/'clean', dynamic, communicate momentum, professionalism etc (as one would imagine from a firm in the financial sector). We like the idea of a reverse-side of the card that includes the logo, and the name and contact details on the other. We expect the deliverable to be whatever format might be required to be able to get cards printed directly by a service such as kelmo press. Our website is www.zub.capital

```html
<!DOCTYPE html>
<html lang="en">
<head>
<meta charset="utf-8">
<title>ZUB Capital – Business Card</title>
<link href="https://fonts.googleapis.com/css2?family=Montserrat:wght@400;500;700&display=swap" rel="stylesheet">
<style>
  :root {
    --bg: #dcdcd9;
    --white: #ffffff;
    --green: #88b14b;
    --green-dark: #324f22;
    --ink: #2a2a2a;
  }
  * { margin: 0; padding: 0; box-sizing: border-box; }
  html, body { width: 1200px; height: 801px; overflow: hidden; }
  body {
    background: var(--bg);
    font-family: "Montserrat", sans-serif;
    position: relative;
  }
  .card {
    position: absolute;
    width: 540px;
    height: 309px;
    overflow: hidden;
    box-shadow: 0 6px 18px rgba(0,0,0,0.18);
  }
  .card-front { left: 80px; top: 90px; background: var(--white); }
  .card-back { left: 580px; top: 420px; background: var(--green); }

  .front-band { position: absolute; inset: 0; width: 540px; height: 309px; }

  .brand-name {
    position: absolute;
    font-weight: 500;
    white-space: nowrap;
  }
  .card-front .brand-name {
    left: 40px; top: 124px;
    font-size: 30px;
    color: var(--green-dark);
  }
  .card-back .brand-name {
    left: 0; right: 0; top: 118px;
    text-align: center;
    font-size: 56px;
    color: var(--white);
  }

  .divider {
    position: absolute;
    left: 262px; top: 40px;
    width: 1px; height: 180px;
    background: var(--green);
  }

  .details {
    position: absolute;
    left: 284px; top: 36px;
    color: var(--ink);
  }
  .person-name {
    font-size: 19px;
    font-weight: 700;
    color: var(--green);
    letter-spacing: 0.5px;
    line-height: 1.1;
  }
  .person-title { font-size: 13px; margin-top: 3px; }
  .contact-list { list-style: none; margin-top: 14px; }
  .contact-list li {
    display: flex; align-items: center; gap: 7px;
    font-size: 12.5px; line-height: 19px;
  }
  .contact-list svg { width: 11px; height: 11px; fill: var(--green); flex: none; }
  .company { margin-top: 14px; font-size: 13px; color: var(--green); line-height: 18px; }
  .city { font-size: 13px; line-height: 18px; }
</style>
</head>
<body>

<section class="card card-front">
  <svg class="front-band" viewBox="0 0 540 309" aria-hidden="true">
    <path d="M30 309 C220 300 420 284 540 262 L540 309 Z" fill="var(--green-dark)"/>
    <path d="M26 309 C220 295 420 278 540 255" fill="none" stroke="var(--green)" stroke-width="2.5"/>
  </svg>

  <div class="brand-name">ZUB Capital</div>
  <div class="divider"></div>

  <div class="details">
    <div class="person-name">MARTEN KOLBE</div>
    <div class="person-title">Managing Director</div>
    <ul class="contact-list">
      <li>
        <svg viewBox="0 0 12 12"><path d="M2 1.5 4 1 5.3 3.6 4.2 4.6C4.8 6 6 7.2 7.4 7.8L8.4 6.7 11 8 10.5 10C6 10.3 1.7 6 2 1.5Z"/></svg>
        +41 79555 0148
      </li>
      <li>
        <svg viewBox="0 0 12 12"><path d="M1 2.5h10v7H1z M1 2.5 6 6.5 11 2.5" fill="var(--green)" stroke="#fff" stroke-width="0.8"/></svg>
        marten@zub.capital
      </li>
      <li>
        <svg viewBox="0 0 12 12"><circle cx="6" cy="6" r="5"/><path d="M1 6h10M6 1c-2 2.6-2 7.4 0 10M6 1c2 2.6 2 7.4 0 10" fill="none" stroke="#fff" stroke-width="0.7"/></svg>
        www.zub.capital
      </li>
    </ul>
    <div class="company">ZUB Capital S.A.</div>
    <div class="city">Basel, Switzerland</div>
  </div>
</section>

<section class="card card-back">
  <div class="brand-name">ZUB Capital</div>
</section>

</body>
</html>
```